SaaS Early tech startup business card design

Unique design for experience ecommerce platform company. the business cards will be used by executive members. conformance with color code is required.

```html
<!DOCTYPE html>
<html lang="en">
<head>
<meta charset="utf-8">
<title>Velto business card</title>
<link href="https://fonts.googleapis.com/css2?family=Montserrat:wght@700;800&family=Roboto:wght@400&display=swap" rel="stylesheet">
<style>
  :root {
    --backdrop: #6b6869;
    --navy: #1f2238;
    --paper: #f7f7f5;
    --teal-deep: #1a5563;
    --teal: #1e8a8e;
    --teal-light: #5cc0b0;
    --ink: #1d1d1f;
    --white: #ffffff;
  }
  * { margin: 0; padding: 0; box-sizing: border-box; }
  html, body { width: 1200px; height: 1200px; overflow: hidden; }
  body { background: var(--backdrop); position: relative; font-family: "Roboto", sans-serif; }

  .card { position: absolute; width: 348px; height: 594px; border-radius: 21px; overflow: hidden; }

  .card-back { left: 200px; top: 298px; background: var(--navy); }
  .card-back .wave-pattern {
    position: absolute; inset: 0;
    background: radial-gradient(ellipse 60% 30% at 50% 22%, rgba(40,90,110,0.18), transparent 70%),
                radial-gradient(ellipse 60% 30% at 50% 80%, rgba(40,90,110,0.18), transparent 70%);
  }
  .card-back .brand {
    position: absolute; left: 0; right: 0; top: 240px; text-align: center;
    font-family: "Montserrat", sans-serif; font-weight: 800; font-size: 92px;
    line-height: 1; color: var(--white); letter-spacing: -1px;
  }
  .card-back .tagline {
    position: absolute; left: 0; right: 0; top: 328px; text-align: center;
    font-size: 15px; letter-spacing: 5px; color: var(--white); padding-left: 5px;
  }

  .card-front { left: 637px; top: 292px; background: var(--paper); }
  .card-front .brand {
    position: absolute; left: 27px; top: 34px;
    font-family: "Montserrat", sans-serif; font-weight: 800; font-size: 80px;
    line-height: 1; color: var(--teal); letter-spacing: -1px;
  }
  .card-front .person {
    position: absolute; left: 28px; top: 170px;
    font-family: "Montserrat", sans-serif; font-weight: 800; font-size: 40px;
    color: var(--teal-deep); line-height: 1;
  }
  .contact { position: absolute; left: 28px; top: 232px; list-style: none; }
  .contact li { display: flex; align-items: center; height: 23.5px; font-size: 17px; color: var(--ink); }
  .contact svg { width: 14px; height: 14px; margin-right: 16px; fill: var(--teal); }
  .address { position: absolute; left: 28px; top: 310px; font-size: 17px; line-height: 23.5px; color: var(--ink); }
  .social { position: absolute; left: 28px; top: 377px; display: flex; gap: 4px; }
  .social span { width: 15px; height: 15px; border-radius: 50%; background: var(--teal); }
  .handle { position: absolute; left: 28px; top: 398px; font-size: 17px; color: var(--ink); }
  .card-front .tagline { position: absolute; left: 28px; top: 536px; font-size: 17px; letter-spacing: 1.2px; color: var(--ink); }
  .card-front .line-art {
    position: absolute; left: 222px; top: 440px; width: 126px; height: 154px;
    background: linear-gradient(160deg, rgba(70,110,160,0.35), rgba(92,192,176,0.45));
    border-top-left-radius: 40px;
  }
</style>
</head>
<body>
  <section class="card card-back">
    <div class="wave-pattern" role="img" aria-label="Faint teal line wave pattern"></div>
    <div class="brand">velto</div>
    <div class="tagline">BUILT AROUND YOU</div>
  </section>

  <section class="card card-front">
    <div class="brand">velto</div>
    <h1 class="person">Karim D.</h1>
    <ul class="contact">
      <li><svg viewBox="0 0 16 16"><path d="M1 6c0-3 14-3 14 0v1h-4V5H5v2H1zM3 8h10l1 6H2zM8 9.5a2 2 0 1 0 0 4 2 2 0 0 0 0-4z"/></svg>(00) 0111 VELT</li>
      <li><svg viewBox="0 0 16 16"><path d="M1 3h14v10H1zM2.5 4.5v7l4-3.5zM13.5 4.5l-4 3.5 4 3.5zM3 4l5 4.5L13 4zM7.2 9l-4.3 3.5h10.2L8.8 9 8 9.7z"/></svg>info@velto.net</li>
      <li><svg viewBox="0 0 16 16"><path d="M8 1a7 7 0 1 0 0 14A7 7 0 0 0 8 1zm-.7 1.6v2.7H5.1c.5-1.4 1.3-2.4 2.2-2.7zm1.4 0c.9.3 1.7 1.3 2.2 2.7H8.7zM4.8 6.7h2.5v2.6H4.8zm3.9 0h2.5v2.6H8.7zM2.5 6.7h1v2.6h-1zm10 0h1v2.6h-1zM5.1 10.7h2.2v2.7c-.9-.3-1.7-1.3-2.2-2.7zm3.6 0h2.2c-.5 1.4-1.3 2.4-2.2 2.7z"/></svg>www.velto.net</li>
    </ul>
    <p class="address">Harbor Tower, Dubai<br>Dubai Media Park, UAE</p>
    <div class="social"><span></span><span></span><span></span><span></span></div>
    <p class="handle">/getvelto</p>
    <p class="tagline">Built around you</p>
    <div class="line-art" role="img" aria-label="Layered teal and blue line motif"></div>
  </section>
</body>
</html>
```